New, modern business card for growing audiology practice

We need a new business card for our audiology practice. Our logo and website have recently changed (more modern) and we want our business cards to reflect this change.
We conduct hearing tests, perform earwax removals, and fit & dispense hearing aids to our patients. We are a family owned practice in which the owner is the one who works directly with the patient. I have attached logos in various formats to use, as well as two ideas I found on this website; as well as a scanned copy of our current logo. Good luck!

Industry/Entity Type

Business

Contact Information for Business Card

Company name: Tolvera Hearing Center
Provider name: Peter Wolstenby, Au.D. F/NSB
Phone number: (440) 683-5127
Address: 837 W. Lindell Ave. Brenford Falls, OH 44318
email: tolverahearing@postvane.com
website: tolverahearing.com

Colors
000000
aaaaaa
dbdbdb
cacaca
9bcb3c
afd23c
cadf82
b1b1b1

Requirements
Must have
• My card must include information in the "details" section. In the attached images, I found a few that I liked and I would like to model after - "brisky bouncin'" and "Sound Method Center".
• Must be horizontal.
• Must include logos provided. I uploaded them in various file formats and various ways.
• Must match logo font, if possible, if not, please get as close as you can.
Nice to have
• I really like the idea of having a color on one side with just the logo and company name and the contact information and provider name on the other side. I also really like the idea of having the main color dominating on the logo/company side with accent of that same color on the contact side of the card.
Should not have
• Must not be vertical.

```html
<!DOCTYPE html>
<html lang="en">
<head>
<meta charset="utf-8">
<title>Tolvera Hearing Center – Business Card</title>
<link href="https://fonts.googleapis.com/css2?family=Lato:wght@400&family=PT+Sans:wght@400;700&display=swap" rel="stylesheet">
<style>
  :root {
    --ink: #000000;
    --charcoal: #2a2a2a;
    --charcoal-deep: #1c1c1c;
    --green: #7aa640;
    --paper: #ffffff;
    --stage: #e6e6e6;
    --text: #1a1a1a;
  }
  * { margin: 0; padding: 0; box-sizing: border-box; }
  html, body { width: 1200px; height: 900px; overflow: hidden; }
  body {
    background: var(--stage);
    font-family: "PT Sans", Arial, sans-serif;
    color: var(--text);
    position: relative;
  }
  .card {
    position: absolute;
    left: 250px;
    width: 700px;
    height: 400px;
    overflow: hidden;
    box-shadow: 0 4px 14px rgba(0,0,0,0.18);
  }
  .card--brand {
    top: 40px;
    background: linear-gradient(135deg, var(--charcoal) 0%, var(--charcoal-deep) 100%);
    display: flex;
    align-items: center;
    justify-content: center;
  }
  .brand-name {
    font-family: "Lato", Arial, sans-serif;
    font-weight: 400;
    letter-spacing: 1px;
    text-transform: uppercase;
    white-space: nowrap;
    display: flex;
    align-items: center;
    gap: 14px;
  }
  .brand-name__dot { width: 14px; height: 14px; border-radius: 50%; flex: none; }
  .card--brand .brand-name { font-size: 36px; color: var(--paper); }
  .card--brand .brand-name__dot { background: var(--paper); }

  .card--contact { top: 460px; background: var(--paper); }
  .card__accents { position: absolute; inset: 0; width: 100%; height: 100%; }
  .provider {
    position: absolute;
    left: 84px; top: 20px;
    font-size: 24px;
    font-weight: 700;
    color: var(--green);
    white-space: nowrap;
  }
  .provider__credentials { font-size: 14px; color: var(--ink); margin-left: 6px; }
  .card--contact .brand-name {
    position: absolute;
    left: 150px; top: 84px;
    font-size: 36px;
    color: var(--ink);
  }
  .card--contact .brand-name__dot { background: var(--green); }
  .address {
    position: absolute;
    left: 60px; top: 156px;
    font-size: 17px;
    line-height: 1.35;
    font-style: normal;
  }
  .contact-list {
    position: absolute;
    left: 60px; top: 220px;
    list-style: none;
    font-size: 17px;
    line-height: 1.45;
  }
  .contact-list li { display: flex; align-items: center; gap: 10px; }
  .contact-list svg { width: 13px; height: 13px; flex: none; }
</style>
</head>
<body>

<section class="card card--brand" aria-label="Card front">
  <div class="brand-name"><span class="brand-name__dot"></span>Tolvera Hearing Center</div>
</section>

<section class="card card--contact" aria-label="Card back">
  <svg class="card__accents" viewBox="0 0 700 400" preserveAspectRatio="none" aria-hidden="true">
    <polygon points="0,0 46,0 0,30" fill="var(--ink)"/>
    <polygon points="58,0 78,0 78,30 36,30" fill="var(--green)"/>
    <polygon points="0,352 292,374 284,400 0,400" fill="var(--ink)"/>
    <polygon points="306,358 700,358 700,400 292,400" fill="var(--green)"/>
  </svg>

  <h1 class="provider">Peter Wolstenby,<span class="provider__credentials">Au.D. F/NSB</span></h1>

  <div class="brand-name"><span class="brand-name__dot"></span>Tolvera Hearing Center</div>

  <address class="address">837 W. Lindell Ave.<br>Brenford Falls, OH 44318</address>

  <ul class="contact-list">
    <li>
      <svg viewBox="0 0 24 24" aria-hidden="true"><path fill="var(--green)" d="M6.6 10.8a15.1 15.1 0 0 0 6.6 6.6l2.2-2.2c.3-.3.7-.4 1-.2 1.1.4 2.3.6 3.6.6.6 0 1 .4 1 1V20c0 .6-.4 1-1 1A17 17 0 0 1 3 4c0-.6.4-1 1-1h3.5c.6 0 1 .4 1 1 0 1.3.2 2.5.6 3.6.1.3 0 .7-.2 1z"/></svg>
      (440) 683-5127
    </li>
    <li>
      <svg viewBox="0 0 24 24" aria-hidden="true"><rect x="2" y="5" width="20" height="14" fill="var(--green)"/><path d="M2 5l10 8 10-8" fill="none" stroke="var(--paper)" stroke-width="1.8"/></svg>
      tolverahearing@postvane.com
    </li>
    <li>
      <svg viewBox="0 0 24 24" aria-hidden="true"><circle cx="12" cy="12" r="10" fill="var(--green)"/><path d="M2 12h20M12 2c3 3 3 17 0 20M12 2c-3 3-3 17 0 20" fill="none" stroke="var(--paper)" stroke-width="1.4"/></svg>
      tolverahearing.com
    </li>
  </ul>
</section>

</body>
</html>
```